MRT Property - Business Cards

Looking for a business card & general letterhead, signage etc design for our new logo.

Colours:
000a20
0056a2
00b5ef
0088ce
68cef2

Fonts:
Poppins
Karla

Please keep look and feel of new brand - example in the zip package I sent.

```html
<!DOCTYPE html>
<html lang="en">
<head>
<meta charset="utf-8">
<title>MRT Property – Business Cards</title>
<link href="https://fonts.googleapis.com/css2?family=Poppins:wght@400;500;600;700&family=Karla:wght@400;500&display=swap" rel="stylesheet">
<style>
  :root {
    --navy-deep: #000a20;
    --card-top: #1b2233;
    --card-bottom: #0e1424;
    --blue-dark: #0056a2;
    --blue-mid: #0088ce;
    --blue-bright: #00b5ef;
    --blue-light: #68cef2;
    --silver: #7d8696;
    --text-light: #e6e9ef;
    --text-soft: #aab1bd;
    --stage: #141518;
  }
  * { box-sizing: border-box; margin: 0; padding: 0; }
  html, body {
    width: 1200px;
    height: 852px;
    overflow: hidden;
    background: var(--stage);
  }
  .card-set {
    position: absolute;
    top: 0; left: 0;
    width: 1200px;
    height: 852px;
    display: flex;
    align-items: center;
    justify-content: center;
    gap: 48px;
  }
  .card {
    position: relative;
    width: 530px;
    height: 304px;
    border-radius: 18px;
    overflow: hidden;
    background: linear-gradient(160deg, var(--card-top), var(--card-bottom));
    box-shadow: 0 10px 30px rgba(0,0,0,.5);
  }
  .brand-name {
    font-family: "Poppins", sans-serif;
    font-weight: 700;
    letter-spacing: .02em;
    white-space: nowrap;
  }

  /* Front */
  .card-front .brand-name {
    position: absolute;
    top: 104px;
    left: 0; right: 0;
    text-align: center;
    font-size: 46px;
    color: var(--silver);
  }
  .card-front .website {
    position: absolute;
    right: 34px;
    bottom: 38px;
    font-family: "Karla", sans-serif;
    font-size: 12px;
    letter-spacing: .42em;
    color: var(--text-soft);
  }
  .card-front .accent-band {
    position: absolute;
    left: 0; right: 0; bottom: 0;
    height: 12px;
    background: var(--blue-dark);
  }

  /* Back */
  .card-back .brand-name {
    position: absolute;
    top: 42px;
    right: 38px;
    font-size: 32px;
    color: var(--blue-mid);
  }
  .contact-person {
    position: absolute;
    left: 34px;
    top: 156px;
  }
  .person-name {
    font-family: "Poppins", sans-serif;
    font-weight: 600;
    font-size: 19px;
    line-height: 1.1;
    color: var(--blue-bright);
  }
  .person-title {
    font-family: "Karla", sans-serif;
    font-size: 12px;
    color: var(--text-light);
    margin-top: 3px;
  }
  .contact-list {
    list-style: none;
    margin-top: 16px;
  }
  .contact-list li {
    display: flex;
    align-items: center;
    gap: 12px;
    font-family: "Karla", sans-serif;
    font-size: 13.5px;
    line-height: 19px;
    color: var(--text-light);
  }
  .contact-list .icon {
    width: 12px;
    height: 12px;
    flex: none;
    fill: var(--blue-mid);
  }
  .contact-list .no-icon { width: 12px; flex: none; }
</style>
</head>
<body>
<main class="card-set">
  <section class="card card-front" aria-label="Business card front">
    <div class="brand-name">MRT Property</div>
    <div class="website">www.mrtproperty.com</div>
    <div class="accent-band"></div>
  </section>

  <section class="card card-back" aria-label="Business card back">
    <div class="brand-name">MRT Property</div>
    <div class="contact-person">
      <div class="person-name">Callum Reid</div>
      <div class="person-title">Associate Director</div>
      <ul class="contact-list">
        <li>
          <svg class="icon" viewBox="0 0 12 12" aria-hidden="true"><path d="M2.4 0.6l2 2.3-1.1 1.4c.8 1.7 2.1 3 3.8 3.8l1.4-1.1 2.3 2-1.2 2.2C4.6 11 1 7.4 .4 1.8z"/></svg>
          <span>555-014-2290</span>
        </li>
        <li>
          <svg class="icon" viewBox="0 0 12 12" aria-hidden="true"><path d="M0 2.5h12v7H0z M.6 3l5.4 3.6L11.4 3" fill="none" stroke="#0088ce" stroke-width="1.2"/></svg>
          <span>callum@mrtproperty.com</span>
        </li>
        <li>
          <svg class="icon" viewBox="0 0 12 12" aria-hidden="true"><circle cx="6" cy="6" r="5.4" fill="none" stroke="#0088ce" stroke-width="1.1"/><path d="M.6 6h10.8M6 .6c-3 3-3 7.8 0 10.8M6 .6c3 3 3 7.8 0 10.8" fill="none" stroke="#0088ce" stroke-width="1"/></svg>
          <span>www.mrtproperty.com</span>
        </li>
        <li>
          <span class="no-icon"></span>
          <span>27 Harbour View Road Northmead</span>
        </li>
      </ul>
    </div>
  </section>
</main>
</body>
</html>
```